German Headhunter/ HR Consultancy needs Business Cards Design

We need a business Card Design for our Company in Stuttgart. We are specialized as Headhunter/ HR Consultancy in Placement of specialist and managers in permanent employment. Please refer to our business logo.

```html
<!DOCTYPE html>
<html lang="en">
<head>
<meta charset="utf-8">
<title>Kernwerk Personalberatung – Business Card</title>
<link rel="stylesheet" href="https://fonts.googleapis.com/css2?family=Arimo:wght@400&family=Montserrat:wght@500;600&display=swap">
<style>
  :root {
    --stage: #9a9a9a;
    --brand-blue: #3853a6;
    --brand-grey: #939498;
    --text-grey: #5f6063;
    --rule-grey: #8c8c8c;
    --paper: #ffffff;
  }
  * { margin: 0; padding: 0; box-sizing: border-box; }
  html, body { width: 1200px; height: 1200px; overflow: hidden; }
  body { background: var(--stage); position: relative; font-family: "Arimo", Arial, sans-serif; }

  .card { position: absolute; top: 303px; width: 370px; height: 594px; background: var(--paper); overflow: hidden; }
  .card--front { left: 200px; }
  .card--back { left: 599px; width: 364px; }

  .front-field { position: absolute; inset: 0; width: 100%; height: 100%; }
  .front-name {
    position: absolute; left: 110px; right: 0; top: 280px;
    text-align: center; color: var(--paper);
    font-family: "Montserrat", Arial, sans-serif; font-weight: 600;
    font-size: 26px; letter-spacing: 1px; line-height: 1.2;
  }

  .brand { position: absolute; left: 34px; top: 111px; display: flex; align-items: center; }
  .brand-square { width: 46px; height: 46px; background: var(--brand-blue); transform: rotate(45deg); margin: 0 18px 0 8px; }
  .brand-rules { display: flex; gap: 7px; margin-right: 9px; height: 84px; align-items: center; }
  .brand-rules span { display: block; width: 2px; background: var(--brand-grey); height: 62px; }
  .brand-rules span.tall { background: var(--brand-blue); height: 84px; }
  .brand-name {
    font-family: "Montserrat", Arial, sans-serif; font-weight: 600;
    color: var(--brand-blue); line-height: 1;
  }
  .brand-name .line-1 { display: block; font-size: 30px; letter-spacing: 1px; }
  .brand-name .line-2 { display: block; font-size: 13.5px; margin-top: 6px; letter-spacing: 0.3px; }

  .person { position: absolute; left: 0; right: 0; top: 341px; text-align: center; }
  .person-name { font-family: "Montserrat", Arial, sans-serif; font-weight: 600; font-size: 24px; color: var(--brand-blue); line-height: 1; }
  .person-role { font-size: 15px; color: var(--text-grey); margin-top: 3px; letter-spacing: 0.3px; line-height: 1.2; }

  .icon-row { position: absolute; left: 87px; width: 189px; top: 396px; height: 25px; display: flex; align-items: center; gap: 5px; }
  .icon-row .rule { flex: 1; height: 1px; background: var(--rule-grey); }
  .icon-row .rule:first-child { margin-right: 2px; }
  .icon-row .rule:last-child { margin-left: 2px; }
  .icon { width: 25px; height: 25px; background: var(--brand-blue); border-radius: 3px; display: flex; align-items: center; justify-content: center; }
  .icon svg { width: 16px; height: 16px; }

  .contact { position: absolute; left: 0; right: 0; top: 432px; text-align: center; font-size: 17px; color: var(--text-grey); line-height: 21.5px; letter-spacing: 0.3px; }
  .contact .accent { color: var(--brand-blue); }
  .divider { position: absolute; left: 88px; width: 194px; top: 507px; height: 1px; background: var(--rule-grey); }
  .address { position: absolute; left: 0; right: 0; top: 518px; text-align: center; font-size: 17px; color: var(--text-grey); line-height: 21.5px; letter-spacing: 0.3px; }
</style>
</head>
<body>

<section class="card card--front" aria-label="Card front">
  <svg class="front-field" viewBox="0 0 370 594" preserveAspectRatio="none" aria-hidden="true">
    <rect width="370" height="594" fill="var(--brand-grey)"/>
    <polygon points="0,0 302,0 0,300 252,549 306,594 0,594" fill="var(--brand-blue)"/>
  </svg>
  <p class="front-name">KERNWERK</p>
</section>

<section class="card card--back" aria-label="Card back">
  <div class="brand">
    <span class="brand-square"></span>
    <div class="brand-rules"><span></span><span class="tall"></span><span></span></div>
    <p class="brand-name"><span class="line-1">KERNWERK</span><span class="line-2">PERSONALBERATUNG</span></p>
  </div>

  <div class="person">
    <p class="person-name">LUKAS BRENNER</p>
    <p class="person-role">MANAGING DIRECTOR</p>
  </div>

  <div class="icon-row">
    <span class="rule"></span>
    <span class="icon" aria-label="Phone">
      <svg viewBox="0 0 16 16"><path d="M2 6c0-2 2-3 6-3s6 1 6 3v1h-3V5.5H5V7H2z M4 8h8l1 5H3z" fill="#fff"/></svg>
    </span>
    <span class="icon" aria-label="Email">
      <svg viewBox="0 0 16 16"><rect x="2" y="4" width="12" height="8" fill="none" stroke="#fff" stroke-width="1.2"/><path d="M2 4l6 5 6-5M2 12l4.5-4M14 12l-4.5-4" fill="none" stroke="#fff" stroke-width="1"/></svg>
    </span>
    <span class="icon" aria-label="Website">
      <svg viewBox="0 0 16 16"><circle cx="8" cy="8" r="6" fill="#fff"/><path d="M5 5.5c1-1 3-.5 3 .8s-2 1-1.5 2.5S5 10 4.5 8.5z M9.5 9c1 0 2 .8 1.5 2.2-.8.4-1.8 0-1.8-1z" fill="var(--brand-blue)"/></svg>
    </span>
    <span class="rule"></span>
  </div>

  <div class="contact">
    <p>0711-482 905 31</p>
    <p>info@kernwerk.de</p>
    <p>www.<span class="accent">kernwerk-hr</span>.de</p>
  </div>
  <div class="divider"></div>
  <div class="address">
    <p>42, Lindenallee 118</p>
    <p>70173 Stuttgart, DE</p>
  </div>
</section>

</body>
</html>
```